RWT Fittings Ltd Business Cards

We need a business card with our business logo. We provide window and door installations on high-rises in west coast British Colombia, Canada.

I would like my business information and details on one side of the card, and the other side the company name with logo

Target Market(s)

General Contractors

Industry/Entity Type

Construction

Contact Information for Business Card

one side i want my company name and logo in the dark theme logo that i provided

Requirements
Must have
• Marco Peltieri, 16045518293, RWTFittings@mailbox-demo.com, 1407-5194 Linden Row Burnaby BC, V5H 2K9, Owner & Manager

```html
<!DOCTYPE html>
<html lang="en">
<head>
<meta charset="utf-8">
<title>RWT Fittings Ltd – Business Cards</title>
<link rel="stylesheet" href="https://fonts.googleapis.com/css2?family=Roboto:wght@400;500;700;900&display=swap">
<style>
  :root {
    --bg: #232323;
    --card: #222227;
    --blue: #27a9e1;
    --grey: #9b9b9b;
    --silver: #c9c9cb;
    --white: #ffffff;
  }
  * { box-sizing: border-box; margin: 0; padding: 0; }
  html, body { width: 1200px; height: 780px; overflow: hidden; background: var(--bg); }
  body { position: relative; font-family: "Roboto", Arial, sans-serif; color: var(--white); }

  .card {
    position: absolute;
    width: 560px;
    height: 320px;
    left: 320px;
    background: var(--card);
    border-radius: 18px;
    border: 3px solid var(--blue);
    overflow: hidden;
    box-shadow: 0 14px 30px rgba(0,0,0,.55);
  }
  .card--front { top: 60px; }
  .card--back { top: 410px; }

  /* wordmark */
  .wordmark { display: flex; align-items: center; gap: 14px; position: absolute; }
  .wordmark__square { background: var(--blue); }
  .wordmark__name { font-weight: 900; letter-spacing: .02em; line-height: 1; white-space: nowrap; }

  .card--front .wordmark { left: 50%; top: 50%; transform: translate(-50%, -50%); }
  .card--front .wordmark__square { width: 42px; height: 42px; }
  .card--front .wordmark__name { font-size: 40px; color: var(--silver); }

  .card--back .wordmark { left: 34px; top: 120px; gap: 10px; }
  .card--back .wordmark__square { width: 26px; height: 26px; }
  .card--back .wordmark__name { font-size: 24px; color: var(--blue); }

  .divider {
    position: absolute; left: 292px; top: 40px;
    width: 2px; height: 190px; background: var(--white);
  }

  .contact { position: absolute; left: 318px; top: 44px; width: 230px; }
  .contact__name { font-size: 25px; font-weight: 700; line-height: 1.05; color: var(--grey); }
  .contact__name .first { color: var(--blue); }
  .contact__role { font-size: 12.5px; font-weight: 500; margin-top: 3px; }
  .contact__address { font-size: 12px; line-height: 1.35; margin-top: 16px; }
  .contact__list { list-style: none; margin-top: 16px; font-size: 12px; line-height: 1.6; }
  .contact__list li { display: flex; align-items: center; gap: 8px; white-space: nowrap; }
  .contact__list svg { width: 13px; height: 13px; flex: none; fill: var(--blue); }

  .band { position: absolute; }
  .band--blue { left: 0; bottom: 10px; width: 300px; height: 16px; background: var(--blue); }
  .band--grey { right: 0; bottom: 38px; width: 220px; height: 14px; background: var(--grey); }
</style>
</head>
<body>

  <section class="card card--front" aria-label="Business card front">
    <div class="wordmark">
      <span class="wordmark__square"></span>
      <span class="wordmark__name">RWT FITTINGS LTD</span>
    </div>
  </section>

  <section class="card card--back" aria-label="Business card back">
    <div class="wordmark">
      <span class="wordmark__square"></span>
      <span class="wordmark__name">RWT FITTINGS LTD</span>
    </div>

    <span class="divider"></span>

    <div class="contact">
      <h1 class="contact__name"><span class="first">Marco</span> Peltieri</h1>
      <p class="contact__role">Owner &amp; Manager</p>
      <p class="contact__address">1407-5194 Linden Row<br>Burnaby BC, V5H 2K9</p>
      <ul class="contact__list">
        <li>
          <svg viewBox="0 0 24 24" aria-hidden="true"><path d="M6.6 10.8a15.1 15.1 0 0 0 6.6 6.6l2.2-2.2c.3-.3.7-.4 1-.2 1.1.4 2.3.6 3.6.6.6 0 1 .4 1 1V20c0 .6-.4 1-1 1A17 17 0 0 1 3 4c0-.6.4-1 1-1h3.5c.6 0 1 .4 1 1 0 1.3.2 2.5.6 3.6.1.3 0 .7-.2 1z"/></svg>
          1604 551 8293
        </li>
        <li>
          <svg viewBox="0 0 24 24" aria-hidden="true"><path d="M3 5h18c.6 0 1 .4 1 1v12c0 .6-.4 1-1 1H3c-.6 0-1-.4-1-1V6c0-.6.4-1 1-1zm9 7.2L20 7H4z"/></svg>
          RWTFittings@mailbox-demo.com
        </li>
      </ul>
    </div>

    <span class="band band--blue"></span>
    <span class="band band--grey"></span>
  </section>

</body>
</html>
```